BrindleStaffing Business Card Design

We are a staffing company finding positions for dedicated nurses and physicians.

Target Market(s)

Business Professionals

Industry/Entity Type

Staffing

Contact Information for Business Card

Gordon Pratley
Chairman
417 39th Avenue South
SAINT PETERSBURG FL 33712
813-555-4172 Mobile
813-555-8036 Fax
gpratley@brindlestaffing.com
www.brindlestaffing.com

Font styles to use
Sans Serif

Colors
fbee3e
f04a50
f37122

Requirements
Must have
• Logo Attached, see colors below. We'd like to see Yellow, Orange and Red.

```html
<!DOCTYPE html>
<html lang="en">
<head>
<meta charset="utf-8">
<title>BrindleStaffing Business Card</title>
<link rel="stylesheet" href="https://fonts.googleapis.com/css2?family=Rubik:wght@400;500;600&display=swap">
<style>
  :root {
    --brand-yellow: #fbee3e;
    --brand-red: #f04a50;
    --brand-orange: #f37122;
    --ink: #1d1d1f;
    --paper: #ececec;
    --backdrop: #d9d9d9;
    --white: #ffffff;
  }
  * { box-sizing: border-box; margin: 0; padding: 0; }
  html, body {
    width: 1200px; height: 1000px; overflow: hidden;
    background: var(--backdrop);
    font-family: "Rubik", sans-serif;
  }
  .sheet {
    position: relative; width: 1200px; height: 1000px;
  }
  .card {
    position: absolute; left: 220px;
    width: 760px; height: 434px;
    box-shadow: 0 10px 28px rgba(0,0,0,0.18);
  }
  .card--front {
    top: 44px;
    background: linear-gradient(90deg, var(--brand-red) 0%, var(--brand-orange) 100%);
  }
  .card--back {
    top: 522px;
    background: var(--paper);
  }
  .wordmark {
    position: absolute; right: 52px; bottom: 52px;
    font-weight: 600; font-size: 46px; letter-spacing: -0.5px;
    display: flex; align-items: center; gap: 10px;
  }
  .wordmark__dot {
    width: 14px; height: 14px; border-radius: 50%;
    background: var(--brand-yellow);
  }
  .card--front .wordmark { color: var(--white); }
  .card--back .wordmark { color: var(--brand-orange); right: 48px; bottom: 150px; }
  .holder {
    position: absolute; left: 52px; top: 48px;
  }
  .holder__name {
    color: var(--brand-orange); font-weight: 600; font-size: 25px;
  }
  .holder__title {
    color: var(--ink); font-size: 17px; margin-top: 4px;
  }
  .contact {
    position: absolute; left: 52px; bottom: 40px;
    color: var(--ink); font-size: 16px; line-height: 1.35;
  }
  .contact__address { margin-bottom: 18px; }
  .contact__list { list-style: none; }
  .contact__item { display: flex; align-items: center; gap: 8px; }
  .contact__icon { width: 13px; height: 13px; fill: var(--brand-orange); flex: none; }
  .contact__brand { color: var(--brand-orange); }
</style>
</head>
<body>
<main class="sheet">
  <section class="card card--front" aria-label="Card front">
    <div class="wordmark"><span class="wordmark__dot"></span>BrindleStaffing</div>
  </section>

  <section class="card card--back" aria-label="Card back">
    <div class="holder">
      <p class="holder__name">Gordon Pratley</p>
      <p class="holder__title">Chairman</p>
    </div>

    <div class="contact">
      <p class="contact__address">417 39th Avenue South<br>SAINT PETERSBURG FL 33712</p>
      <ul class="contact__list">
        <li class="contact__item">
          <svg class="contact__icon" viewBox="0 0 16 16"><path d="M3 1l3 3-1.5 2a9 9 0 0 0 5.5 5.5L12 10l3 3-2 2C7 15 1 9 1 3z"/></svg>
          813-555-4172
        </li>
        <li class="contact__item">
          <svg class="contact__icon" viewBox="0 0 16 16"><rect x="4" y="1" width="8" height="4"/><rect x="1" y="6" width="14" height="6" rx="1"/><rect x="4" y="10" width="8" height="5"/></svg>
          813-555-8036
        </li>
        <li class="contact__item">
          <svg class="contact__icon" viewBox="0 0 16 16"><path d="M1 3h14v10H1z M1 3l7 6 7-6" stroke="#ececec" stroke-width="1"/></svg>
          gpratley@brindlestaffing.com
        </li>
        <li class="contact__item">
          <svg class="contact__icon" viewBox="0 0 16 16"><circle cx="8" cy="8" r="7"/><path d="M1 8h14M8 1c-3 4-3 10 0 14M8 1c3 4 3 10 0 14" stroke="#ececec" stroke-width="1" fill="none"/></svg>
          <span>www.<span class="contact__brand">brindlestaffing</span>.com</span>
        </li>
      </ul>
    </div>

    <div class="wordmark"><span class="wordmark__dot"></span>BrindleStaffing</div>
  </section>
</main>
</body>
</html>
```